New florist business website design

Number 1 want is an easy to navigate & check out website
Needs to be beautiful and eye catching as well.
This is an online only business (no shop front)
Rustic and blush pinks, neutrals, woods, leaves
Customers need to be able to go onto my website, select something they want to buy but have the option to use a drop down box to change colours of the flowers, or add notes to make changes to the arrangement

Industry/Entity Type

Florist

Coding

Coded - Design and coding required

Number of Pages Required

5+ page

Colors
f9d9e8
fff2ec
fffefc

Requirements
Must have
• Drop down menu to take you to other pages for Arrangements, bouquets, everlasting arrangements, gifts, contact
Be able to purchase and “add to basket”
Checkout page
Nice to have
• Be able to add my own photos once I’ve taken new ones
Should not have
• Tacky images or clip art

```html
<!DOCTYPE html>
<html lang="en">
<head>
<meta charset="utf-8">
<title>Bloom &amp; Linen — Florist</title>
<link rel="stylesheet" href="https://fonts.googleapis.com/css2?family=Jost:wght@400;500&family=Allura&family=Arimo:wght@400&display=swap">
<style>
:root{
  --blush:#f9d9e8;
  --peach:#fff2ec;
  --cream:#fffefc;
  --footer:#fcedf1;
  --ink:#1c1a1a;
  --muted:#5a5555;
  --icon-bg:#fde3d2;
  --ink-bar:#0b0b0b;
  --badge:#e9ecf3;
}
*{box-sizing:border-box;margin:0;padding:0}
html,body{width:1200px;height:4866px;overflow:hidden}
body{position:relative;background:var(--cream);color:var(--ink);font-family:"Jost",sans-serif}
.abs{position:absolute}
.script{font-family:"Allura",cursive;font-weight:400}
.body-text{font-family:"Arimo",sans-serif;font-size:11px;line-height:18px;color:var(--muted)}
.btn{position:absolute;display:flex;align-items:center;justify-content:center;gap:8px;border:2px solid var(--ink);border-radius:30px;font:500 12px "Jost",sans-serif;letter-spacing:1px;background:transparent;color:var(--ink)}
.center{left:0;width:1200px;text-align:center}

.top-bar{top:0;left:0;width:1200px;height:26px;background:var(--ink-bar);color:#fff;font:500 12px "Jost",sans-serif;text-align:center;line-height:26px}

.hero{top:26px;left:0;width:1200px;height:804px;background:linear-gradient(180deg,#f8eef0 0%,#f6e6ea 55%,#fffefc 100%)}
.hero-photo{top:110px;left:640px;width:520px;height:560px;border-radius:40px;background:radial-gradient(ellipse at 45% 30%,#f2803a 0%,#f4a06a 28%,#efe7e4 60%,rgba(246,230,234,0) 78%)}
.main-nav{top:60px;left:72px;display:flex;gap:34px;font-size:13px}
.brand{top:80px;left:0;width:1200px;text-align:center;font:400 30px "Jost",sans-serif;color:var(--ink)}
.nav-icons{top:56px;left:950px;display:flex;gap:40px}
.hero-kicker{top:318px;left:74px;font-size:25px;letter-spacing:1.5px}
.hero-title{top:352px;left:76px;font-size:88px;line-height:1}
.dots{display:flex;gap:8px;justify-content:center}
.dots i{width:7px;height:7px;border-radius:50%;background:var(--ink);display:block}
.dots i.on{width:9px;height:9px;background:var(--blush);border:1px solid var(--ink);margin-top:-1px}

.perks{top:850px;left:0;width:1200px;height:150px}
.perk{position:absolute;top:0;width:320px;text-align:center}
.perk-icon{width:76px;height:76px;border-radius:50%;background:var(--icon-bg);margin:0 auto;display:flex;align-items:center;justify-content:center}
.perk-name{font-size:24px;margin-top:10px;line-height:1}
.perk-note{font-size:12px;margin-top:8px;letter-spacing:.3px}
.perk-rule{position:absolute;top:36px;width:1px;height:106px;background:#bbb}

.sec-kicker{font-size:34px;line-height:1}
.sec-title{font-size:36px;line-height:1;font-weight:400}

.product{position:absolute;top:1304px;width:232px;height:396px;text-align:center}
.product.active{background:var(--peach);border-radius:24px;box-shadow:0 4px 18px rgba(240,190,170,.25)}
.product-photo{width:130px;height:180px;margin:30px auto 0;border-radius:60px 60px 30px 30px}
.product-name{margin-top:50px;font-size:16px}
.product-price{font-size:36px;line-height:1.2;font-weight:500}
.arrow{position:absolute;top:1480px}

.welcome-band{top:1955px;left:0;width:1200px;height:407px;background:var(--blush)}
.welcome-photo{top:1918px;left:597px;width:603px;height:410px;border-radius:24px 0 0 24px;background:linear-gradient(135deg,#6a5a60 0%,#b8a0c8 35%,#e6d2c4 60%,#8c7d86 100%)}

.quote{top:2612px;left:200px;width:820px;font-size:11px;line-height:18px;text-align:center;color:var(--ink)}

.post{position:absolute;top:3080px;width:322px;text-align:center}
.post-photo{height:226px;border-radius:30px}
.post-date{width:54px;height:54px;border-radius:50%;background:var(--peach);margin:-28px auto 0;position:relative;font-size:12px;line-height:14px;padding-top:13px}
.post-title{font-size:26px;margin-top:12px}
.post-text{margin-top:10px;font-size:11px;line-height:18px;color:var(--muted);font-family:"Arimo",sans-serif;padding:0 12px}
.read-more{margin-top:20px;font-size:12px;color:#777;text-decoration:underline}

.gallery{top:3901px;left:70px;width:1048px;height:210px;display:flex}
.gallery span{flex:1;display:block}

.news{top:4292px;left:0;width:1200px;height:147px;background:var(--peach)}
.news-input{top:4360px;left:675px;width:304px;height:37px;border:2px solid var(--ink);border-radius:20px;font:italic 12px "Arimo",sans-serif;padding:10px 18px}
.news-btn{top:4360px;left:986px;width:132px;height:37px;border:2px solid var(--ink);border-radius:20px;font:500 12px "Jost",sans-serif;letter-spacing:1px;display:flex;align-items:center;justify-content:center}

.site-footer{top:4439px;left:0;width:1200px;height:390px;background:var(--footer)}
.foot-brand{top:4600px;left:72px;font-size:44px;line-height:1}
.foot-head{top:4528px;font-size:27px}
.foot-list{list-style:none;font-size:12px;line-height:13px}
.contact-row{display:flex;gap:14px;font-size:12px;line-height:14px;margin-bottom:12px}
.social-row{display:flex;gap:12px;align-items:center;font-size:12px;margin-bottom:10px}
.social-row i{width:13px;height:13px;border-radius:50%;background:var(--ink);display:block}

.bottom-bar{top:4829px;left:0;width:1200px;height:37px;background:var(--ink-bar);color:#fff;font-size:12px}
.pay{display:flex;gap:6px;position:absolute;right:76px;top:7px}
.pay span{width:44px;height:24px;border-radius:3px;background:var(--badge);color:var(--ink);font:500 8px "Jost",sans-serif;display:flex;align-items:center;justify-content:center;white-space:nowrap;overflow:hidden}
</style>
</head>
<body>

<div class="abs top-bar">Free Shipping 2 days delivery time</div>

<section class="abs hero">
  <div class="abs hero-photo" role="img" aria-label="Orange lilies in a white lace vase on a soft pink table"></div>
</section>
<nav class="abs main-nav"><span>Home</span><span>Shop</span><span>About</span><span>Blogs</span><span>Contact</span></nav>
<div class="abs brand">Bloom &amp; Linen</div>
<div class="abs nav-icons">
  <svg width="26" height="26" viewBox="0 0 26 26" fill="none" stroke="#1c1a1a" stroke-width="1.8"><circle cx="18" cy="8" r="5"/><path d="M14 12 4 22M7 19l3 3"/></svg>
  <svg width="32" height="30" viewBox="0 0 32 30" fill="none" stroke="#1c1a1a" stroke-width="1.8"><path d="M4 9h20l-2 17H6z"/><path d="M9 9a5 5 0 0 1 10 0"/><circle cx="25" cy="23" r="6" fill="#1c1a1a"/><text x="25" y="26" font-size="8" fill="#fff" stroke="none" text-anchor="middle" font-family="Jost,sans-serif">2</text></svg>
  <svg width="32" height="26" viewBox="0 0 32 26" stroke="#1c1a1a" stroke-width="2.2"><path d="M2 4h28M10 13h20M2 22h28"/></svg>
</div>
<div class="abs hero-kicker">GORGEOUS FLOWERS FOR YOUR</div>
<div class="abs hero-title script">Special Events</div>
<div class="btn" style="top:495px;left:80px;width:170px;height:46px">SHOP NOW</div>
<div class="abs dots center" style="top:682px"><i></i><i class="on"></i><i></i></div>

<section class="abs perks">
  <div class="perk" style="left:82px">
    <div class="perk-icon"><svg width="34" height="34" viewBox="0 0 34 34" fill="none" stroke="#1c1a1a" stroke-width="1.6"><path d="M4 16 30 6l-8 24-5-10z"/><path d="M17 20 30 6"/></svg></div>
    <div class="perk-name script">Free Shipping</div>
    <div class="perk-note">GET A FREE DELIVERY ON ORDERS OF $200</div>
  </div>
  <div class="perk-rule" style="left:420px"></div>
  <div class="perk" style="left:441px">
    <div class="perk-icon"><svg width="32" height="32" viewBox="0 0 32 32" fill="none" stroke="#1c1a1a" stroke-width="1.7"><path d="M7 4l5 1 2 6-3 3a16 16 0 0 0 7 7l3-3 6 2 1 5-4 3C13 27 5 19 4 8z"/></svg></div>
    <div class="perk-name script">Free Support</div>
    <div class="perk-note">24/7 CUSTOMER SERVICE</div>
  </div>
  <div class="perk-rule" style="left:795px"></div>
  <div class="perk" style="left:813px">
    <div class="perk-icon" style="font-size:30px">$</div>
    <div class="perk-name script">Price Guarantee</div>
    <div class="perk-note">WE GUARANTEE THE BEST PRICE</div>
  </div>
</section>

<div class="abs center sec-kicker script" style="top:1110px">Wonderful Flowers</div>
<h2 class="abs center sec-title" style="top:1156px">Feature Products</h2>

<svg class="arrow" style="left:56px" width="18" height="30" viewBox="0 0 18 30" fill="none" stroke="#888" stroke-width="2"><path d="M15 2 3 15l12 13"/></svg>
<svg class="arrow" style="left:1120px" width="18" height="30" viewBox="0 0 18 30" fill="none" stroke="#888" stroke-width="2"><path d="M3 2l12 13L3 28"/></svg>

<article class="product" style="left:101px">
  <div class="product-photo" role="img" aria-label="Bouquet of red carnations wrapped in pink paper" style="background:linear-gradient(180deg,#d8232f 0%,#e24a58 50%,#f6bfcc 100%)"></div>
  <div class="product-name">Name of product # 01</div>
  <div class="product-price">$40</div>
</article>
<article class="product active" style="left:361px">
  <div class="product-photo" role="img" aria-label="Bouquet of pink and white lisianthus in pink wrap" style="background:linear-gradient(180deg,#b3306e 0%,#e48ab5 55%,#f8d3e4 100%)"></div>
  <div class="product-name">Name of product # 01</div>
  <div class="product-price">$40</div>
  <div class="btn" style="top:332px;left:42px;width:138px;height:38px;font-size:11px;letter-spacing:0">Add To Cart
    <svg width="16" height="16" viewBox="0 0 16 16" fill="none" stroke="#1c1a1a" stroke-width="1.4"><path d="M2 5h12l-1 9H3z"/><path d="M5 5a3 3 0 0 1 6 0"/></svg>
  </div>
</article>
<article class="product" style="left:621px">
  <div class="product-photo" role="img" aria-label="Bunch of red tulips tied with twine" style="background:linear-gradient(180deg,#c81e4a 0%,#d65470 40%,#6a8a4a 100%)"></div>
  <div class="product-name">Name of product # 01</div>
  <div class="product-price">$40</div>
</article>
<article class="product" style="left:870px">
  <div class="product-photo" role="img" aria-label="Bouquet of white calla lilies" style="background:linear-gradient(180deg,#f4f3ee 0%,#e6ead8 55%,#9bb083 100%)"></div>
  <div class="product-name">Name of product # 01</div>
  <div class="product-price">$40</div>
</article>

<div class="btn" style="top:1782px;left:510px;width:168px;height:47px">BROWSE MORE</div>

<section class="abs welcome-band"></section>
<div class="abs welcome-photo" role="img" aria-label="Rows of wrapped mixed flower bouquets at a market"></div>
<div class="abs script" style="top:2014px;left:78px;font-size:34px">Welcome</div>
<h2 class="abs" style="top:2060px;left:78px;font-size:37px;font-weight:400;line-height:45px">Exclusive Design by<br>Best Florists</h2>
<p class="abs body-text" style="top:2180px;left:78px;width:370px">Lorem Ipsum is simply dummy text of the printing and typesetting industry. Lorem Ipsum has been the industry's standard dummy text ever since the 1500s.</p>
<div class="btn" style="top:2263px;left:80px;width:170px;height:48px">SHOP NOW</div>

<div class="abs center sec-kicker script" style="top:2446px">Reviews</div>
<h2 class="abs center sec-title" style="top:2492px">Testimonials</h2>
<div class="abs" style="top:2600px;left:182px;font-size:40px;line-height:1">&ldquo;</div>
<p class="abs quote">Lorem Ipsum is simply dummy text of the printing and typesetting industry. Lorem Ipsum has been the industry's standard dummy text ever since the 1500s, when an unknown printer took a galley of type and scrambled it to make a type specimen book. It has survived not only five centuries, but also the leap into electronic typesetting, remaining essentially unchanged.</p>
<div class="abs" style="top:2640px;left:784px;font-size:40px;line-height:1">&rdquo;</div>
<div class="abs center script" style="top:2690px;font-size:30px">Maria</div>
<div class="abs dots center" style="top:2752px"><i></i><i class="on"></i><i></i></div>

<div class="abs center sec-kicker script" style="top:2895px">Articles</div>
<h2 class="abs center sec-title" style="top:2943px">Blog Posts</h2>

<article class="post" style="left:79px">
  <div class="post-photo" role="img" aria-label="Pink cherry blossom branches on white" style="background:linear-gradient(135deg,#f1e6e4 0%,#e8a3b6 45%,#f4dfe5 100%)"></div>
  <div class="post-date">june<br>2,2021</div>
  <h3 class="post-title" style="font-weight:400">Artcle title # 01</h3>
  <p class="post-text">Lorem Ipsum is simply dummy text of the printing and typesetting industry. Lorem Ipsum has been the industry's standard dummy text ever since the 1500s.</p>
  <div class="read-more">Read More &raquo;</div>
</article>
<article class="post" style="left:438px">
  <div class="post-photo" role="img" aria-label="Magenta chrysanthemum blooms" style="background:linear-gradient(135deg,#9b2fb0 0%,#c94ad0 50%,#7a1f8e 100%)"></div>
  <div class="post-date">june<br>2,2021</div>
  <h3 class="post-title" style="font-weight:400">Artcle title # 02</h3>
  <p class="post-text">Lorem Ipsum is simply dummy text of the printing and typesetting industry. Lorem Ipsum has been the industry's standard dummy text ever since the 1500s.</p>
  <div class="read-more">Read More &raquo;</div>
</article>
<article class="post" style="left:799px">
  <div class="post-photo" role="img" aria-label="Orange and pink dahlias and mums" style="background:linear-gradient(135deg,#e8821f 0%,#f0a23a 40%,#d47ab8 100%)"></div>
  <div class="post-date">june<br>2,2021</div>
  <h3 class="post-title" style="font-weight:400">Artcle title # 03</h3>
  <p class="post-text">Lorem Ipsum is simply dummy text of the printing and typesetting industry. Lorem Ipsum has been the industry's standard dummy text ever since the 1500s.</p>
  <div class="read-more">Read More &raquo;</div>
</article>

<div class="btn" style="top:3561px;left:512px;width:170px;height:48px">BROWSE MORE</div>

<div class="abs center sec-kicker script" style="top:3735px">Follow us on</div>
<h2 class="abs center sec-title" style="top:3780px">Petalgram</h2>
<div class="abs gallery">
  <span role="img" aria-label="Pale peach peony bouquet" style="background:linear-gradient(180deg,#f1e1dc,#e5c6bf)"></span>
  <span role="img" aria-label="Blue hydrangea and white rose bouquet" style="background:linear-gradient(180deg,#7fa0cc,#6f8a46)"></span>
  <span role="img" aria-label="Purple lisianthus bouquet" style="background:linear-gradient(180deg,#8a6ccc,#5b3a98)"></span>
  <span role="img" aria-label="Pink rose bouquet" style="background:linear-gradient(180deg,#f19aa8,#d86a84)"></span>
  <span role="img" aria-label="Purple and pink mixed bouquet" style="background:linear-gradient(180deg,#9c6aa8,#c06aa8)"></span>
</div>
<div class="btn" style="top:4164px;left:509px;width:170px;height:47px">FOLLOW US
  <svg width="20" height="20" viewBox="0 0 20 20" fill="none" stroke="#1c1a1a" stroke-width="1.6"><rect x="2" y="2" width="16" height="16" rx="3"/></svg>
</div>

<section class="abs news"></section>
<h2 class="abs" style="top:4328px;left:74px;font-size:27px;font-weight:400">Join us for our latest news updates</h2>
<p class="abs body-text" style="top:4380px;left:74px;width:560px;font-size:10.5px;line-height:16px">Lorem Ipsum is simply dummy text of the printing and typesetting industry. Lorem Ipsum has been the industry's standard dummy text ever since the 1500s.</p>
<div class="abs news-input">Email Address</div>
<div class="abs news-btn">SUBSCRIBE</div>

<footer class="abs site-footer"></footer>
<div class="abs foot-brand">Bloom &amp; Linen</div>
<h3 class="abs foot-head" style="left:467px;font-weight:400">Quick links</h3>
<ul class="abs foot-list" style="top:4612px;left:469px">
  <li>Home</li><li>Shop</li><li>About</li><li>Blogs</li><li>Contact</li><li>Arrangement</li><li>bouquets</li><li>everlasting arrangements</li><li>gifts</li>
</ul>
<h3 class="abs foot-head" style="left:705px;font-weight:400">Contact info.</h3>
<div class="abs" style="top:4614px;left:710px">
  <div class="contact-row"><svg width="10" height="14" viewBox="0 0 10 14"><path d="M5 0a5 5 0 0 1 5 5c0 4-5 9-5 9S0 9 0 5a5 5 0 0 1 5-5z" fill="#1c1a1a"/><circle cx="5" cy="5" r="2" fill="#fff"/></svg><span>1420 Willow Ln.<br>Fairbrook, CA 90210</span></div>
  <div class="contact-row"><svg width="11" height="11" viewBox="0 0 32 32"><path d="M7 4l5 1 2 6-3 3a16 16 0 0 0 7 7l3-3 6 2 1 5-4 3C13 27 5 19 4 8z" fill="#1c1a1a"/></svg><span>(+00) 555 204 318</span></div>
  <div class="contact-row"><svg width="11" height="9" viewBox="0 0 11 9"><rect width="11" height="9" fill="#1c1a1a"/><path d="M0 0l5.5 5L11 0" stroke="#fff" fill="none"/></svg><span>hello@bloomandlinen.com</span></div>
</div>
<h3 class="abs foot-head" style="left:979px;font-weight:400">Social Links</h3>
<div class="abs" style="top:4614px;left:986px">
  <div class="social-row"><i></i>Petalbook</div>
  <div class="social-row"><i></i>Wrenly</div>
  <div class="social-row"><i></i>Postvine</div>
  <div class="social-row"><i></i>Petalgram</div>
  <div class="social-row"><i></i>Pinstem</div>
</div>

<div class="abs bottom-bar">
  <span class="abs" style="left:72px;top:10px">Copyright &copy; 2021 Bloom &amp; Linen &nbsp;/&nbsp; Privacy Policy</span>
  <div class="pay"><span>Zentrip</span><span>Plumora</span><span>Kavix</span><span>Orlent</span><span>Tessival</span></div>
</div>

</body>
</html>
```